Brisk Haven - Business Card

Modern Business Card : I like a simple, clean designs. Think Pear!

Information to Include
Brisk Haven Inc. (Logo)
Name: Ned Farrow
Position: President
Office: 555-318-2046
Fax: 555-318-2046
Cell: 555-318-2046
E-Mail: nfarrow@thebriskhaven.example
Website: www.thebriskhaven.example

I attached the "guardnet.example" dealer logo. This logo is not a requirement, but a plus if it looks good with the design.

I also have access to more pictures and logos, if you see something on guardnet.example
or vexlo.example, I can probably get the file. Again, this is not mandatory.

```html
<!DOCTYPE html>
<html lang="en">
<head>
<meta charset="utf-8">
<title>Brisk Haven – Business Card</title>
<link rel="stylesheet" href="https://fonts.googleapis.com/css2?family=Roboto:wght@300;400;700&display=swap">
<style>
  :root {
    --backdrop: #dcd9d4;
    --card: #f0f0ef;
    --ink: #2b2b2b;
    --ink-soft: #555555;
    --accent: #d5582a;
    --shadow: rgba(0, 0, 0, 0.18);
  }
  * { box-sizing: border-box; margin: 0; padding: 0; }
  html, body {
    width: 1200px;
    height: 900px;
    overflow: hidden;
  }
  body {
    background: var(--backdrop);
    font-family: "Roboto", "Helvetica Neue", Arial, sans-serif;
    color: var(--ink);
    display: flex;
    flex-direction: column;
    align-items: center;
    justify-content: center;
    gap: 60px;
  }
  .card {
    position: relative;
    width: 560px;
    height: 320px;
    background: var(--card);
    box-shadow: 0 6px 18px var(--shadow);
  }

  /* Front */
  .card--front {
    display: flex;
    align-items: center;
    justify-content: center;
  }
  .wordmark {
    display: flex;
    align-items: center;
    gap: 14px;
  }
  .wordmark__square {
    width: 44px;
    height: 44px;
    background: var(--accent);
  }
  .wordmark__name {
    font-weight: 700;
    font-size: 34px;
    letter-spacing: -0.5px;
    color: var(--accent);
  }

  /* Back */
  .card--back .wordmark {
    position: absolute;
    left: 44px;
    top: 46px;
    gap: 10px;
  }
  .card--back .wordmark__square { width: 30px; height: 30px; }
  .card--back .wordmark__name { font-size: 22px; }

  .holder {
    position: absolute;
    left: 44px;
    top: 168px;
  }
  .holder__name {
    font-weight: 300;
    font-size: 22px;
    letter-spacing: 0.5px;
    text-transform: uppercase;
    color: var(--ink);
  }
  .holder__title {
    font-weight: 400;
    font-size: 14px;
    color: var(--ink-soft);
    margin-top: 2px;
  }
  .website {
    position: absolute;
    left: 44px;
    bottom: 46px;
    font-size: 14px;
    color: var(--ink);
  }
  .website__domain {
    font-weight: 700;
    color: var(--accent);
  }

  .contacts {
    position: absolute;
    right: 36px;
    top: 60px;
    list-style: none;
    font-size: 13px;
    line-height: 1.9;
    color: var(--ink);
  }
  .contacts__label {
    display: inline-block;
    width: 22px;
    color: var(--accent);
  }
</style>
</head>
<body>
  <section class="card card--front" aria-label="Business card front">
    <div class="wordmark">
      <span class="wordmark__square"></span>
      <span class="wordmark__name">Brisk Haven</span>
    </div>
  </section>

  <section class="card card--back" aria-label="Business card back">
    <div class="wordmark">
      <span class="wordmark__square"></span>
      <span class="wordmark__name">Brisk Haven</span>
    </div>

    <ul class="contacts">
      <li><span class="contacts__label">T</span>555-318-2046</li>
      <li><span class="contacts__label">F</span>555-318-2046</li>
      <li><span class="contacts__label">M</span>555-318-2046</li>
      <li><span class="contacts__label">E</span>nfarrow@thebriskhaven.example</li>
    </ul>

    <div class="holder">
      <p class="holder__name">Ned Farrow</p>
      <p class="holder__title">President</p>
    </div>

    <p class="website">www.<span class="website__domain">thebriskhaven</span>.example</p>
  </section>
</body>
</html>
```